Upstart Retirement Planning Firm needs help with business card design

Harborview Nest Advisors, LLC is looking for help with business card design. We give advice on investments, insurance, and other financial matters related to retirement. There are some required disclosures that we will provide but mostly we are looking for a professional, classy business card that reflects the theme we have chosen. We have a logo that is attached but we would like to add a phrase; "Turning Your Earned Income Into Retirement Income"

Doubled sided only so that we can add the required disclosures (needed for our industry) on the back of the card. We will provide the exact words for this in 1-2 days.

Target Market(s)

Retirees and Pre-retirees. Professionals 50+ years old

Industry/Entity Type

Financial Planning

Contact Information for Business Card

We currently have two people who will need separate cards so we'd like to have a template so that we can add names for new cards in the future.

For the first run, please show the following information.

Gregor Pelham, MBA, ChFC®, CLU®
Financial Advisor, Registered Representative
gpelham@harborviewnest.example
Phone: (555) 318-2946
Toll Free Fax: (800) 555-0193

Address is
2187 Meadowlark Ridge Rd.
Suite K418
Virginia Beach, VA 23999

Colors
3277b5

Requirements
Must have
• Logo, contact info, small phase to describe business (in description), required legal disclosures on back of the card as follows (in small font)
• Gregor Pelham is a registered representative of and offers securities through Brightmoor Capital Brokerage Corporation, Member FNQX. Brightmoor Capital Brokerage Corporation is a member of the Brightmoor Capital Alliance which is the marketing name for Brightmoor Holding Corporation and its affiliates.
Nice to have
• Rounded edges, raised letters
Should not have
• any colors that aren't in the logo (other than black for font)

```html
<!DOCTYPE html>
<html lang="en">
<head>
<meta charset="utf-8">
<title>Harborview Nest Advisors – Business Card</title>
<link rel="stylesheet" href="https://fonts.googleapis.com/css2?family=Tinos:wght@400;700&display=swap">
<style>
  :root {
    --brand-blue: #2d5a9e;
    --ring-grey: #9a9a9a;
    --card-white: #ffffff;
    --page-bg: #ecebe8;
    --ink: #1a1a1a;
    --ink-soft: #4a4a4a;
  }
  * { box-sizing: border-box; margin: 0; padding: 0; }
  html, body {
    width: 1200px; height: 902px; overflow: hidden;
    background: var(--page-bg);
    font-family: "Tinos", "Times New Roman", serif;
    color: var(--ink);
  }
  .card {
    position: absolute; left: 290px;
    width: 620px; height: 354px;
    border-radius: 14px; overflow: hidden;
    box-shadow: 0 4px 14px rgba(0,0,0,.18);
    background: var(--card-white);
  }
  .card--back { top: 60px; }
  .card--front { top: 474px; }
  .card__art { position: absolute; inset: 0; width: 100%; height: 100%; }
  .card__content {
    position: absolute; inset: 0;
    display: flex; flex-direction: column; align-items: center;
    text-align: center;
  }
  .brand-name {
    color: var(--brand-blue); font-weight: 700;
    display: flex; align-items: center; gap: 10px;
  }
  .brand-name__dot {
    width: 14px; height: 14px; border-radius: 50%;
    background: var(--ring-grey);
  }

  /* Back */
  .card--back .card__content { justify-content: center; padding: 0 110px; }
  .card--back .brand-name { font-size: 34px; }
  .brand-rule {
    width: 300px; height: 1px; background: var(--ring-grey);
    margin: 16px 0 18px;
  }
  .disclosure {
    font-size: 11px; line-height: 1.45; color: var(--ink-soft);
    max-width: 380px;
  }

  /* Front */
  .card--front .card__content { padding-top: 28px; }
  .card--front .brand-name { font-size: 22px; }
  .tagline {
    margin-top: 5px; font-size: 13px; color: var(--ring-grey);
    letter-spacing: .3px;
  }
  .divider {
    width: 350px; height: 2px; background: var(--brand-blue);
    margin: 10px 0 10px;
  }
  .person-name { color: var(--brand-blue); font-weight: 700; font-size: 28px; line-height: 1.1; }
  .credentials, .job-title { font-size: 16px; line-height: 1.3; }
  .contact { margin-top: 10px; font-size: 14px; line-height: 1.45; }
  .address { font-size: 13px; }
</style>
</head>
<body>

  <section class="card card--back" aria-label="Card back">
    <svg class="card__art" viewBox="0 0 620 354" aria-hidden="true">
      <rect width="620" height="354" fill="var(--ring-grey)"/>
      <ellipse cx="310" cy="177" rx="290" ry="320" fill="var(--card-white)"/>
    </svg>
    <div class="card__content">
      <div class="brand-name"><span class="brand-name__dot"></span>Harborview Nest Advisors, LLC</div>
      <div class="brand-rule"></div>
      <p class="disclosure">Gregor Pelham is a registered representative of and offers securities through Brightmoor Capital Brokerage Corporation, Member FNQX. Brightmoor Capital Brokerage Corporation is a member of the Brightmoor Capital Alliance which is the marketing name for Brightmoor Holding Corporation and its affiliates.</p>
    </div>
  </section>

  <section class="card card--front" aria-label="Card front">
    <svg class="card__art" viewBox="0 0 620 354" aria-hidden="true">
      <rect width="620" height="354" fill="var(--brand-blue)"/>
      <ellipse cx="310" cy="177" rx="285" ry="300" fill="var(--ring-grey)"/>
      <ellipse cx="310" cy="177" rx="271" ry="292" fill="var(--card-white)"/>
    </svg>
    <div class="card__content">
      <div class="brand-name"><span class="brand-name__dot"></span>Harborview Nest Advisors, LLC</div>
      <div class="tagline">Turning Your Earned Income Into Retirement Income</div>
      <div class="divider"></div>
      <div class="person-name">Gregor Pelham</div>
      <div class="credentials">MBA, ChFC®, CLU®</div>
      <div class="job-title">Financial Advisor, Registered Representative</div>
      <div class="contact">
        <div>(555) 318-2946</div>
        <div>(800) 555-0193</div>
        <div>gpelham@harborviewnest.example</div>
        <div class="address">2187 Meadowlark Ridge Rd. Suite K418 Virginia Beach, VA 23999</div>
      </div>
    </div>
  </section>

</body>
</html>
```